Need business card with a logo for a hearing aid sales and audiology business. We have two Hearing Instrument Specialists and one Audiologist on staff. Over 25 years in business. Locally owned and operated. Financing available. Most insurances accepted.

Summit Audio Wellness LLC
48730 W Larchmont, Suite 7
Spokane, WA 99281
509-617-2084
www.summitaudiowell.example

Manager
Tobias Kerrell HIS COHC
License #71829046

Target Market(s)

50yr old + people with a hearing loss.

Industry/Entity Type

Business

Contact Information for Business Card

48730 W Larchmont, Suite 7
Spokane, WA 99281
509-617-2084
www.summitaudiowell.example

Manager
Tobias Kerrell HIS COHC
NLVE #71829046

Font styles to use
Serif
Sans Serif

Requirements
Must have
• Business name, Tobias's name and title(s) and contact information, License #, web address

```html
<!DOCTYPE html>
<html lang="en">
<head>
<meta charset="utf-8">
<title>Summit Audio Wellness LLC – Business Card</title>
<link href="https://fonts.googleapis.com/css2?family=Open+Sans:wght@400;600;700&display=swap" rel="stylesheet">
<style>
  :root {
    --backdrop: #000000;
    --card: #343537;
    --ink: #ffffff;
    --ink-soft: #e4e4e4;
    --rule: #4a4b4e;
  }
  html, body {
    margin: 0;
    padding: 0;
    width: 1200px;
    height: 900px;
    overflow: hidden;
    background: var(--backdrop);
  }
  .stage {
    position: relative;
    width: 1200px;
    height: 900px;
    font-family: "Open Sans", Arial, sans-serif;
    color: var(--ink);
  }
  .card {
    position: absolute;
    top: 271px;
    width: 457px;
    height: 281px;
    background: var(--card);
    border-radius: 14px;
  }
  .card--front { left: 137px; }
  .card--back { left: 626px; }

  /* front: brand block */
  .front-brand {
    position: absolute;
    left: 40px;
    top: 80px;
    width: 140px;
    text-align: center;
  }
  .front-brand .mark {
    display: block;
    width: 54px;
    height: 54px;
    margin: 0 auto 12px;
    border-radius: 50%;
    background: var(--ink);
  }
  .front-brand .brand-name {
    font-size: 13px;
    font-weight: 600;
    line-height: 17px;
    color: var(--ink);
  }

  .divider {
    position: absolute;
    left: 208px;
    top: 80px;
    width: 1px;
    height: 200px;
    background: var(--rule);
  }

  /* front: contact details */
  .details {
    position: absolute;
    left: 234px;
    top: 62px;
  }
  .person-name {
    margin: 0;
    font-size: 15px;
    font-weight: 700;
    line-height: 20px;
  }
  .person-name .credentials {
    font-size: 12px;
    font-weight: 600;
  }
  .role {
    margin: 2px 0 0;
    font-size: 12.5px;
    color: var(--ink-soft);
  }
  .license {
    margin: 16px 0 0;
    font-size: 12.5px;
    font-weight: 700;
  }
  .contact-list {
    list-style: none;
    margin: 16px 0 0;
    padding: 0;
    font-size: 12.5px;
    color: var(--ink-soft);
  }
  .contact-list li {
    display: flex;
    align-items: center;
    height: 17px;
  }
  .contact-list svg {
    width: 10px;
    height: 10px;
    margin-right: 8px;
    fill: var(--ink);
  }
  .address {
    margin: 11px 0 0 -3px;
    font-size: 12.5px;
    line-height: 17px;
    color: var(--ink-soft);
    font-style: normal;
  }

  /* back: brand lockup */
  .back-brand {
    position: absolute;
    left: 0;
    right: 0;
    top: 64px;
    text-align: center;
  }
  .back-brand .mark {
    display: block;
    width: 78px;
    height: 78px;
    margin: 0 auto 22px;
    border-radius: 50%;
    background: var(--ink);
  }
  .back-brand .brand-name {
    font-size: 20px;
    font-weight: 600;
    letter-spacing: 2px;
    line-height: 25px;
    text-transform: uppercase;
    color: var(--ink);
  }
</style>
</head>
<body>
<main class="stage">
  <section class="card card--front" aria-label="Business card front">
    <div class="front-brand">
      <span class="mark" aria-hidden="true"></span>
      <div class="brand-name">Summit Audio<br>Wellness LLC</div>
    </div>
    <div class="divider" aria-hidden="true"></div>
    <div class="details">
      <h1 class="person-name">Tobias Kerrell <span class="credentials">HIS COHC</span></h1>
      <p class="role">Manager</p>
      <p class="license">License #71829046</p>
      <ul class="contact-list">
        <li>
          <svg viewBox="0 0 24 24" aria-hidden="true"><path d="M6.6 10.8a15.1 15.1 0 0 0 6.6 6.6l2.2-2.2c.3-.3.7-.4 1-.2 1.1.4 2.3.6 3.6.6.6 0 1 .4 1 1V20c0 .6-.4 1-1 1A17 17 0 0 1 3 4c0-.6.4-1 1-1h3.5c.6 0 1 .4 1 1 0 1.3.2 2.5.6 3.6.1.3 0 .7-.2 1z"/></svg>
          509-617-2084
        </li>
        <li>
          <svg viewBox="0 0 24 24" aria-hidden="true"><circle cx="12" cy="12" r="11"/></svg>
          www.summitaudiowell.example
        </li>
      </ul>
      <address class="address">48730 W Larchmont, Suite 7<br>Spokane, WA 99281</address>
    </div>
  </section>

  <section class="card card--back" aria-label="Business card back">
    <div class="back-brand">
      <span class="mark" aria-hidden="true"></span>
      <div class="brand-name">Summit Audio<br>Wellness LLC</div>
    </div>
  </section>
</main>
</body>
</html>
```